Veterinary Pylon

My veterinary clinic is not clearly visible from the street and I want to place a Pylon next to my driveway. I want a modern, elegant straight Design, the Photo shows the sheduled place. One can see the clinic on our Homepage: www.tailbright-vethaus.at
The last pictures are examples for pylones I like

Target Market(s)

the passing cars often miss my entry...I want to show where to turn left

Colors
3276b5
33a6d7
00a990

Requirements
Must have
• High value, simple elegance, size: 250cm (high) x 100cm (width)
Nice to have
• Our Logo, arrow(?)

A special Text is not necessary but this will be an option:

Biegen sie hier ab und wir biegen es wieder hin!
Should not have
• Too much Color, the colors I have chosen are the possible colors but it‘s not necessary to use them.

```html
<!DOCTYPE html>
<html lang="de">
<head>
<meta charset="utf-8">
<title>Tailbright Vethaus – Pylon</title>
<link rel="stylesheet" href="https://fonts.googleapis.com/css2?family=Archivo+Black&display=swap">
<style>
  :root {
    --navy: #114a93;
    --sky: #2ebde0;
    --arrow-deep: #1e6fae;
    --paper: #ffffff;
  }
  html, body {
    margin: 0;
    padding: 0;
    width: 1200px;
    height: 3000px;
    overflow: hidden;
    background: var(--paper);
  }
  .pylon {
    position: relative;
    width: 1200px;
    height: 3000px;
    background: var(--paper);
    overflow: hidden;
  }
  .base-chevron {
    position: absolute;
    left: 0;
    top: 0;
    width: 1200px;
    height: 3000px;
  }
  .brand-dot {
    position: absolute;
    left: 430px;
    top: 110px;
    width: 340px;
    height: 340px;
    border-radius: 50%;
    background: var(--sky);
  }
  .brand-name {
    position: absolute;
    left: 0;
    width: 1200px;
    margin: 0;
    text-align: center;
    font-family: "Archivo Black", sans-serif;
    font-weight: 400;
    font-size: 132px;
    line-height: 1.1;
    letter-spacing: 2px;
    text-transform: uppercase;
  }
  .brand-name--top {
    top: 590px;
    color: var(--navy);
  }
  .brand-name--base {
    top: 2600px;
    color: var(--paper);
  }
  .direction-arrow {
    position: absolute;
    left: 0;
    top: 1280px;
    width: 1200px;
    height: 320px;
  }
</style>
</head>
<body>
  <main class="pylon">
    <svg class="base-chevron" viewBox="0 0 1200 3000" aria-hidden="true">
      <polygon fill="var(--sky)" points="0,1530 612,1864 1200,1544 1200,3000 0,3000"/>
      <polygon fill="var(--navy)" points="0,1550 612,1919 1200,1565 1200,3000 0,3000"/>
    </svg>

    <div class="brand-dot" aria-hidden="true"></div>
    <h1 class="brand-name brand-name--top">Tailbright<br>Vethaus</h1>

    <svg class="direction-arrow" viewBox="0 1280 1200 320" role="img" aria-label="Pfeil nach links – hier abbiegen">
      <defs>
        <linearGradient id="arrowFade" x1="439" y1="0" x2="792" y2="0" gradientUnits="userSpaceOnUse">
          <stop offset="0" stop-color="var(--arrow-deep)"/>
          <stop offset="1" stop-color="var(--sky)"/>
        </linearGradient>
      </defs>
      <polygon fill="url(#arrowFade)"
        points="439,1435 577,1299 577,1342 498,1421 792,1421 792,1450 498,1450 577,1530 577,1573"/>
    </svg>

    <p class="brand-name brand-name--base">Tailbright<br>Vethaus</p>
  </main>
</body>
</html>
```